Create a premium soap bar box bar design for an all-natural, men's skincare brand.

We are launching a men’s premium, natural soap bar and skincare business. To start, we will be launching cold-press, all-natural soap bars with a few additional products such as lotions. We plan to expand our line into additional skincare products such as face exfoliants, moisturizers and cleansers that target basic needs such as anti-aging, clarifying and hydrating.

Our target audience is men ages 25-50, with a secondary audience of male teens. Our target audience are mid to high income, professionals that live in more urban areas, but enjoy being active outdoors after work and on the weekends. Our target audience are hard workers, humble and want to enjoy all that life has to offer – whether that’s on top of a mountain or an ocean wave. They hike, bike, skateboard, surf or any other sport that gets them outside. They are husbands, brothers and fathers – there for their family and friends.

Our brand is sophisticated, adventurous and has a sense of humor. Many of our competitors either focus on the rugged outdoors or are more pretentious. We are in-between. We are free spirited and love the fresh air. Our products are trustworthy with no toxic chemicals or harsh ingredients. We are all-natural and provide high-quality, premium products that our audience expects and deserves.

Target Market(s)

Men, ages 25-54 who are high-earning professionals, yet enjoy getting outdoors and being active on the weekends - hiking, biking, surfing, skateboarding and more.

Industry/Entity Type

Men's skincare

Font styles to use
Sans Serif

Requirements
Must have
• See attachments
Nice to have
• We would prefer to a have a premium, slightly more modern looking design that will appeal to our target audience and slightly higher price point.
Should not have
• Please do not include an icon for the fragrance, i.e. cinnamon sticks. However, we do need some differentiation for the fragrance, i.e. color, etc. as it will be on the shelf with other fragrances.

```html
<!DOCTYPE html>
<html lang="en">
<head>
<meta charset="utf-8">
<title>Cinnamon Bark – Men's Natural Soap Box</title>
<link rel="stylesheet" href="https://fonts.googleapis.com/css2?family=Montserrat:wght@400;500;700;800;900&display=swap">
<style>
  :root {
    --backdrop: #e4e5e7;
    --kraft: #c9a57a;
    --kraft-light: #d4b38b;
    --navy: #0d2745;
    --coral: #e6564a;
    --ink: #1a1d22;
  }
  * { margin: 0; padding: 0; box-sizing: border-box; }
  html, body { width: 1200px; height: 857px; overflow: hidden; }
  body {
    background: var(--backdrop);
    font-family: "Montserrat", sans-serif;
    position: relative;
  }

  /* End panel */
  .box-end {
    position: absolute;
    left: 140px; top: 70px;
    width: 170px; height: 440px;
    background: linear-gradient(180deg, var(--kraft-light), var(--kraft));
    border-right: 1px solid rgba(0,0,0,.18);
    display: flex; align-items: center; justify-content: center;
  }
  .end-brand {
    transform: rotate(90deg);
    display: flex; align-items: center; gap: 14px;
    white-space: nowrap;
  }
  .end-brand .brand-dot { width: 18px; height: 18px; border-radius: 50%; background: var(--coral); }
  .end-brand .brand-name {
    color: var(--navy);
    font-weight: 700; font-size: 34px; letter-spacing: 3px;
  }

  /* Top panel */
  .box-top {
    position: absolute;
    left: 310px; top: 70px;
    width: 750px; height: 440px;
    background: linear-gradient(135deg, var(--kraft-light), var(--kraft));
    overflow: hidden;
  }
  .brand-band {
    position: absolute;
    left: 40px; top: 0;
    width: 170px; height: 360px;
    background: var(--navy);
    display: flex; align-items: center; justify-content: center;
  }
  .band-brand {
    transform: rotate(-90deg);
    display: flex; align-items: center; gap: 12px;
    white-space: nowrap;
  }
  .brand-dot { width: 14px; height: 14px; border-radius: 50%; background: var(--coral); }
  .band-brand .brand-name {
    color: var(--kraft-light);
    font-weight: 500; font-size: 28px; letter-spacing: 3px;
  }
  .title-rule {
    position: absolute;
    left: 260px; top: 34px;
    width: 450px; height: 6px;
    background: var(--navy);
  }
  .product-title {
    position: absolute;
    left: 260px; top: 58px;
    color: var(--navy);
    font-weight: 900; font-size: 62px; line-height: .95;
    letter-spacing: 1px;
  }
  .scene-art {
    position: absolute;
    left: 470px; top: 150px;
    width: 240px; height: 150px;
    background: radial-gradient(ellipse at 50% 60%, #ec7a6e, var(--coral));
    border-radius: 6px;
  }
  .product-type {
    position: absolute;
    right: 40px; top: 322px;
    color: var(--navy);
    font-weight: 800; font-size: 19px; letter-spacing: 1px;
  }
  .bottom-band {
    position: absolute;
    left: 0; bottom: 0;
    width: 100%; height: 80px;
    background: var(--navy);
  }
  .net-weight {
    position: absolute;
    left: 300px; top: 26px;
    color: var(--kraft-light);
    font-weight: 700; font-size: 22px;
  }
  .net-weight span { font-size: 16px; font-weight: 500; }

  /* Front panel */
  .box-front {
    position: absolute;
    left: 310px; top: 510px;
    width: 750px; height: 190px;
    background: linear-gradient(180deg, var(--kraft), var(--kraft-light));
    border-top: 1px solid rgba(0,0,0,.18);
  }
  .front-band { height: 44px; background: var(--navy); }
  .front-copy {
    padding: 16px 40px 0 40px;
    color: var(--ink);
    font-size: 16px; line-height: 1.4;
  }
  .front-copy strong { font-weight: 700; display: block; }
</style>
</head>
<body>
  <section class="box-end">
    <div class="end-brand">
      <span class="brand-dot"></span>
      <span class="brand-name">RIDGE HALE</span>
    </div>
  </section>

  <section class="box-top">
    <div class="brand-band">
      <div class="band-brand">
        <span class="brand-dot"></span>
        <span class="brand-name">RIDGE HALE</span>
      </div>
    </div>
    <div class="title-rule"></div>
    <h1 class="product-title">CINNAMON<br>BARK</h1>
    <div class="scene-art" role="img" aria-label="Coral illustration of a forest clearing with pine trees and a man relaxing in a hammock"></div>
    <p class="product-type">MEN’S NATURAL SOAP</p>
    <div class="bottom-band">
      <p class="net-weight">5 <span>oz. bar</span></p>
    </div>
  </section>

  <section class="box-front">
    <div class="front-band"></div>
    <p class="front-copy">
      <strong>Real Ingredients for Real Guys.</strong>
      Bring the outdoors in using real, natural ingredients on your skin. Traditional bar soap contains harsh chemical ingredients that can be harmful to you and the environment. Lather up with Ridge Hale’s handcrafted, all-natural soap and feel the difference.
    </p>
  </section>
</body>
</html>
```